Business card design for new eCommerce site focusing on integrity and strong businsess tactics

We need a business card that will stand out and be memorable. Something with color that matches our company logo colors. Think high end version of Pactivo. There are 2 logos provided. The parent company is called Amber Ledge Partners and we are presenting a new and very exciting eCommerce site called BrightHarborTrade.example.

Target Market(s)

Our target markets are in the Activities, Food and Beverage, Health and Beauty

Industry/Entity Type

Marketing

Contact Information for Business Card

We have 4 members that need cards...I will provide all info to the winner of the design contest
Business Address is
4870 West 63rd Avenue, Suite C207
Phoenix AZ 85731

Font styles to use
Serif
Sans Serif

Colors

Designer to choose colors to be used in the design.

Requirements
Must have
• The card must be memorable...should be unique in design but must exude integrity and be playful .
• I have provided several colors or our parent company...please feel free to use which ever
Nice to have
• I will leave this up to you. Feel free to use other images of your choosing that wraps around our client.....Activities, Dining, Health, Beauty
Should not have
• just dont be boring

```html
<!DOCTYPE html>
<html lang="en">
<head>
<meta charset="utf-8">
<title>Amber Ledge Partners – Business Cards</title>
<link rel="stylesheet" href="https://fonts.googleapis.com/css2?family=Roboto:wght@400;500;700&family=Roboto+Condensed:wght@500;700&family=Questrial&display=swap">
<style>
  :root {
    --backdrop: #2a2a2a;
    --card-dark: #1c1d1f;
    --card-light: #f1f1f1;
    --brand-green: #8dc63f;
    --swoosh-green: #7cbf2f;
    --brand-blue: #2c7db4;
    --ink-grey: #555555;
    --white: #ffffff;
  }
  * { margin: 0; padding: 0; box-sizing: border-box; }
  html, body { width: 1200px; height: 960px; overflow: hidden; }
  body {
    background: var(--backdrop);
    position: relative;
    font-family: "Roboto", Arial, sans-serif;
  }

  .card {
    position: absolute;
    border-radius: 18px;
    overflow: hidden;
  }

  /* Front: parent company */
  .card-front {
    left: 320px; top: 108px;
    width: 602px; height: 344px;
    background: var(--card-dark);
  }
  .front-mark {
    position: absolute;
    left: 227px; top: 68px;
    width: 148px; height: 148px;
    border-radius: 50%;
    background: var(--brand-green);
  }
  .front-name {
    position: absolute;
    left: 0; right: 0; top: 224px;
    text-align: center;
    font-family: "Roboto", Arial, sans-serif;
    font-weight: 700;
    font-size: 31px;
    color: var(--brand-green);
  }

  /* Back: personal card */
  .card-back {
    left: 320px; top: 493px;
    width: 600px; height: 342px;
    background: var(--card-light);
  }
  .card-back svg.wave { position: absolute; left: 0; top: 0; }

  .site-mark {
    position: absolute;
    left: 192px; top: 48px;
    width: 64px; height: 64px;
    border-radius: 50%;
    background: var(--brand-blue);
  }
  .site-name {
    position: absolute;
    left: 270px; top: 62px;
    font-family: "Roboto", Arial, sans-serif;
    font-weight: 500;
    font-size: 21px;
    color: var(--brand-green);
  }
  .site-tagline {
    position: absolute;
    left: 272px; top: 96px;
    font-family: "Questrial", Arial, sans-serif;
    font-size: 15.5px;
    letter-spacing: 0.4px;
    color: var(--ink-grey);
  }

  .contact-list {
    position: absolute;
    left: 30px; top: 202px;
    list-style: none;
    color: var(--white);
    font-size: 14px;
    line-height: 19px;
  }
  .contact-list li { display: flex; align-items: center; gap: 7px; }
  .contact-list svg { width: 13px; height: 13px; flex: none; }
  .contact-address {
    position: absolute;
    left: 30px; top: 281px;
    color: var(--white);
    font-size: 14px;
    line-height: 19px;
    font-style: normal;
  }

  .holder-name {
    position: absolute;
    left: 303px; top: 274px;
    font-family: "Roboto Condensed", Arial, sans-serif;
    font-weight: 700;
    font-size: 21px;
    color: var(--white);
  }
  .holder-title {
    position: absolute;
    left: 318px; top: 300px;
    font-family: "Roboto Condensed", Arial, sans-serif;
    font-weight: 700;
    font-size: 14px;
    color: var(--brand-green);
  }
</style>
</head>
<body>

  <section class="card card-front" aria-label="Amber Ledge Partners card front">
    <div class="front-mark"></div>
    <div class="front-name">Amber Ledge Partners</div>
  </section>

  <section class="card card-back" aria-label="BrightHarborTrade card back">
    <svg class="wave" width="600" height="342" viewBox="0 0 600 342" aria-hidden="true">
      <path fill="var(--swoosh-green)"
        d="M92,30 C104,100 128,150 178,172 C238,196 400,176 478,214 C522,236 548,290 562,342 H0 V0 Z"/>
      <path fill="var(--brand-blue)" stroke="var(--white)" stroke-width="3"
        d="M88,-2 C100,80 122,160 172,192 C232,228 384,206 470,238 C512,254 540,300 555,344 H-2 V-2 Z"/>
    </svg>

    <div class="site-mark"></div>
    <div class="site-name">BrightHarborTrade.example</div>
    <div class="site-tagline">Activities-Dining-Health-Beauty</div>

    <ul class="contact-list">
      <li>
        <svg viewBox="0 0 16 16"><path fill="var(--brand-green)" d="M3.6 1.2l2.3 2.6-1.2 1.8c.9 1.9 2.4 3.4 4.4 4.5l1.8-1.2 2.6 2.3-1.5 2.5C6.8 13.3 2.5 9 1.2 3z"/></svg>
        555 210 4471
      </li>
      <li>
        <svg viewBox="0 0 16 16"><rect x="4" y="1" width="8" height="14" rx="1.5" fill="none" stroke="var(--brand-green)" stroke-width="1.6"/><circle cx="8" cy="12.5" r="0.9" fill="var(--brand-green)"/></svg>
        555 382 0196
      </li>
      <li>
        <svg viewBox="0 0 16 16"><rect x="1" y="3" width="14" height="10" fill="var(--brand-green)"/><path d="M1 3l7 6 7-6" fill="none" stroke="var(--brand-blue)" stroke-width="1.3"/></svg>
        dana@brightharbortrade.example
      </li>
      <li>
        <svg viewBox="0 0 16 16"><circle cx="8" cy="8" r="7" fill="var(--brand-green)"/><path d="M1 8h14M8 1c-3 3.5-3 10.5 0 14M8 1c3 3.5 3 10.5 0 14" fill="none" stroke="var(--brand-blue)" stroke-width="1"/></svg>
        www.brightharbortrade.example
      </li>
    </ul>

    <address class="contact-address">
      4870 West 63rd Avenue<br>
      Suite C207, Phoenix AZ 85731
    </address>

    <div class="holder-name">DANA WHITFIELD</div>
    <div class="holder-title">CEO/FOUNDER</div>
  </section>

</body>
</html>
```